High Tech Real Estate Startup needs a business card

We are developing an innovative real estate marketing product based around advanced search and virtual reality.

We talk to people, we need business cards.

Target Market(s)

The target market is technology professionals and realtors.

Contact Information for Business Card

The information to be included will include

Name
Title
Phone Number
E-mail Address
www.zelquin.com

It should use simple iconography for each one of those fields.

Font styles to use
Other font styles liked:
• Co, Jubilat, Avenir

Colors

Designer to choose colors to be used in the design.

Requirements
Must have
• Clean aesthetic,
• Good use of negative space.
• It should use our company logo, shown in the attached file. It is able to use the negative of that logo (coloured font and white background) and I have attached other acceptable accent colours in a swatch file.
Should not have
• Should not be too busy
• No extraneous text (slogans, tag lines etc)

```html
<!DOCTYPE html>
<html lang="en">
<head>
<meta charset="utf-8">
<title>Zelquin Business Card</title>
<link rel="stylesheet" href="https://fonts.googleapis.com/css2?family=Montserrat:wght@500&family=Roboto+Condensed:wght@400;700&display=swap">
<style>
  :root {
    --teal: #00b8be;
    --teal-light: #2cc6cb;
    --white: #ffffff;
    --ink: #3a3a3a;
    --backdrop: #2b2b2b;
  }
  * { margin: 0; padding: 0; box-sizing: border-box; }
  html, body { width: 1200px; height: 911px; overflow: hidden; }
  body {
    background: var(--backdrop);
    display: flex;
    align-items: center;
    justify-content: center;
    gap: 40px;
  }
  .card {
    position: relative;
    width: 540px;
    height: 309px;
    overflow: hidden;
    box-shadow: 0 12px 30px rgba(0,0,0,0.45);
  }
  .card-front { background: var(--white); }
  .card-back { background: var(--teal); }
  .front-sweep { position: absolute; inset: 0; width: 100%; height: 100%; }
  .wordmark {
    position: absolute;
    font-family: "Montserrat", sans-serif;
    font-weight: 500;
    color: var(--white);
    letter-spacing: 2px;
    line-height: 1;
    white-space: nowrap;
  }
  .card-front .wordmark { left: 26px; bottom: 58px; font-size: 40px; }
  .card-back .wordmark { left: 96px; top: 102px; font-size: 64px; }
  .back-url {
    position: absolute;
    left: 100px;
    top: 196px;
    font-family: "Montserrat", sans-serif;
    font-weight: 500;
    font-size: 12px;
    letter-spacing: 5px;
    color: var(--white);
  }
  .contact {
    position: absolute;
    right: 24px;
    top: 62px;
    text-align: right;
    font-family: "Roboto Condensed", sans-serif;
    color: var(--ink);
    white-space: nowrap;
  }
  .contact-name { font-size: 21px; font-weight: 700; color: var(--teal); letter-spacing: 0.5px; }
  .contact-title { font-size: 14px; margin-top: 2px; margin-bottom: 8px; letter-spacing: 0.5px; }
  .contact-line {
    display: flex;
    justify-content: flex-end;
    align-items: center;
    gap: 6px;
    font-size: 13px;
    line-height: 19px;
  }
  .contact-icon { width: 11px; height: 11px; fill: var(--teal); }
</style>
</head>
<body>
  <section class="card card-front" aria-label="Card front">
    <svg class="front-sweep" viewBox="0 0 540 309" preserveAspectRatio="none" aria-hidden="true">
      <path d="M0,0 L300,0 C340,110 320,230 200,309 L0,309 Z" fill="var(--teal)"/>
      <path d="M0,0 L250,0 C270,120 200,230 0,290 Z" fill="var(--teal-light)" opacity="0.35"/>
      <path d="M285,10 C318,115 300,225 190,300 C290,222 305,115 285,10 Z" fill="var(--white)"/>
    </svg>
    <div class="wordmark">ZELQUIN</div>
    <div class="contact">
      <div class="contact-name">DANA WHITFIELD</div>
      <div class="contact-title">CEO/FOUNDER</div>
      <div class="contact-line">555 014 2290
        <svg class="contact-icon" viewBox="0 0 12 12" aria-hidden="true"><path d="M2.5 0.5 L4.5 0.5 L5.2 3.2 L3.8 4.3 C4.5 6 6 7.5 7.7 8.2 L8.8 6.8 L11.5 7.5 L11.5 9.5 C11.5 10.8 10.5 11.5 9.5 11.5 C4.5 11 1 7.5 0.5 2.5 C0.5 1.3 1.3 0.5 2.5 0.5 Z"/></svg>
      </div>
      <div class="contact-line">dana@zelquin.com
        <svg class="contact-icon" viewBox="0 0 12 12" aria-hidden="true"><rect x="0" y="0" width="12" height="12" rx="2"/><path d="M2 3.5 L6 6.5 L10 3.5 M2 3.5 H10 V8.5 H2 Z" fill="none" stroke="#fff" stroke-width="1"/></svg>
      </div>
      <div class="contact-line">www.zelquin.com
        <svg class="contact-icon" viewBox="0 0 12 12" aria-hidden="true"><circle cx="6" cy="6" r="6"/><path d="M1 6 H11 M6 1 C3.5 3.5 3.5 8.5 6 11 M6 1 C8.5 3.5 8.5 8.5 6 11" fill="none" stroke="#fff" stroke-width="0.9"/></svg>
      </div>
    </div>
  </section>

  <section class="card card-back" aria-label="Card back">
    <div class="wordmark">ZELQUIN</div>
    <div class="back-url">WWW.ZELQUIN.COM</div>
  </section>
</body>
</html>
```